Willow Nest Product Marketing Sheet Front and Back

Please see the VERY VERY VERY ROUGH COMPS THAT WE DID TO LEND SOME DIRECTION TO THE PIECE- SO YOU HAVE AN IDEA OF WHAT'S IMPORTANT TO COMMUNICATE ON THE FRONT AND THE BACK.

DON'T FOLLOW OUR LAYOUT.. This is just for you to see what goes to the front and what goes to the back.. see the files that we just loaded up to the art folder!

We also have a PDF that has a check off list for items that need to be on the front and then on the back!

PROJECT SCOPE:

Project is to make a sell sheet front that is 8.5 inches wide x 11 inches tall in a 4 color design using our current Willow Nest Logo with your design talents. We also need the back of the sell sheet that has the basic instructions on how to install the Willow Nest Mattress Cover and shows the value added aspects of the product.

We need files in layered PSD format as we have various dealers that we tweak parts of our product line. We will also use these layered files as a back up for the printer in case they don't have the printer font, we can make him print ready file from your PSD file.

We have the logo, tag line, header main font selected and need you to design the look and feel of the piece.

We have all of the copy for the sell sheet- this is the only PDF file in the art file resources.

Overall this piece needs to convey a FUN, FRESH and PEACEFUL PRODUCT.. we don't want a cluttered design.

COPY IS SAVED AS: WILLOW NEST CONTENTS ( PDF FILE)
COMPS ARE SAVED AS: FRONT AND REAR COMP ( JPG FILES)
Updates

Project Deadline Extended
Reason: We have a lot of designers that have requested a few more days to submit.. so we are extending the competition. Thank you and good luck!

Target Market(s)

Corvani Consumers that are buying a mattress cover for comfort, peace of mind and to reduce night heat issues ( sweating) and to avoid dust mites, bed bugs and stains.

Industry/Entity Type

Marketing

Font styles to use
Sans Serif

Colors
f37122
f68e4e
fabb94
0393ce
33a6d7
86cae7
ffffff
add136
fbee3d

Requirements
Must have
• Our Current Logo as the center piece..
• WILLOW NEST is the brand name
• For a peaceful night sleep is the tag line
• Value Points ( see the PDF attached)
• Crisp color, Clean Fonts, Cant be cluttered.
• File Construction- Must be a PSD file 8.5 x11 and 300 DPI for printing
Nice to have
• Clean, Easy to Read and consistent from the front to the back
Should not have
• We don't want a cluttered look and feel for this marketing piece.

```html
<!DOCTYPE html>
<html lang="en">
<head>
<meta charset="utf-8">
<title>Willow Nest Sell Sheet – Front and Back</title>
<link href="https://fonts.googleapis.com/css2?family=Baloo+2:wght@400;500;600;700&display=swap" rel="stylesheet">
<style>
  :root {
    --stage: #3a3a3a;
    --paper: #ffffff;
    --purple: #8b6dad;
    --purple-deep: #7a5aa0;
    --magenta: #b55fae;
    --magenta-soft: #c77fc0;
    --ink: #3b3b3b;
    --gold: #e0a82a;
    --mist: #ececee;
  }
  * { margin: 0; padding: 0; box-sizing: border-box; }
  html, body { width: 1200px; height: 798px; overflow: hidden; background: var(--stage); }
  .canvas { position: relative; width: 1200px; height: 798px; }
  .sheet { position: absolute; top: 82px; width: 497px; height: 643px; background: var(--paper); }
  .sheet--front { left: 74px; }
  .sheet--back { left: 623px; }
  .sheet svg { display: block; width: 497px; height: 643px; font-family: "Baloo 2", sans-serif; }
  .brand-name { fill: var(--gold); font-weight: 700; font-size: 19px; letter-spacing: 0.5px; }
  .brand-dot { fill: var(--gold); }
  .tagline { font-size: 24px; font-weight: 500; }
  .tagline .t-lead { fill: var(--purple); }
  .tagline .t-main { fill: var(--magenta); }
  .subline { fill: var(--ink); font-size: 12.5px; font-weight: 500; }
  .check-item { fill: var(--purple); font-size: 15px; font-weight: 600; }
  .check-mark { fill: none; stroke: var(--purple); stroke-width: 1.3; }
  .badge-disc { fill: var(--magenta); stroke: var(--purple); stroke-width: 1.5; }
  .badge-ring { fill: none; stroke: #fff; stroke-width: 2; }
  .badge-slash { stroke: #fff; stroke-width: 2; }
  .badge-glyph { fill: #fff; }
  .badge-line { fill: none; stroke: #fff; stroke-width: 2; stroke-linecap: round; }
  .badge-label { fill: var(--purple-deep); font-size: 11px; font-weight: 600; }
  .badge-label--small { font-size: 8.5px; }
  .fit-note { fill: var(--purple); font-size: 25px; font-weight: 600; }
  .steps-band { fill: var(--purple); }
  .steps-title { fill: #fff; font-size: 23px; font-weight: 600; letter-spacing: 0.4px; }
  .step-disc { fill: #fff; }
  .step-text { fill: #b9b9b9; font-size: 7.5px; }
  .step-arrow { fill: none; stroke: #fff; stroke-width: 1.2; }
  .sizes-title { fill: var(--purple); font-size: 19px; font-weight: 600; }
  .sizes-list { fill: var(--ink); font-size: 14.5px; font-weight: 500; }
  .rule { stroke: #555; stroke-width: 0.8; }
  .offer-title { fill: var(--purple); font-size: 19px; font-weight: 600; }
  .offer-text { fill: var(--ink); font-size: 17.5px; font-weight: 500; }
</style>
</head>
<body>
<main class="canvas">

  <!-- FRONT -->
  <section class="sheet sheet--front" aria-label="Sell sheet front">
    <svg viewBox="0 0 497 643" xmlns="http://www.w3.org/2000/svg">
      <defs>
        <linearGradient id="sleeperFill" x1="0" y1="0" x2="1" y2="0">
          <stop offset="0" stop-color="#ffffff"/>
          <stop offset="0.35" stop-color="#efe6e2"/>
          <stop offset="0.7" stop-color="#f3eeee"/>
          <stop offset="1" stop-color="#f7f6f8"/>
        </linearGradient>
        <linearGradient id="sleeperFade" x1="0" y1="0" x2="0" y2="1">
          <stop offset="0.7" stop-color="#fff" stop-opacity="0"/>
          <stop offset="1" stop-color="#fff" stop-opacity="1"/>
        </linearGradient>
        <linearGradient id="floorFront" x1="0" y1="0" x2="0" y2="1">
          <stop offset="0" stop-color="#ffffff"/>
          <stop offset="0.3" stop-color="#eeeef0"/>
          <stop offset="1" stop-color="#e2e2e5"/>
        </linearGradient>
        <path id="arcL" d="M -39.3 27.5 A 48 48 0 1 1 39.3 27.5"/>
        <path id="arcS" d="M -29.5 20.6 A 36 36 0 1 1 29.5 20.6"/>
      </defs>

      <rect x="0" y="466" width="497" height="177" fill="url(#floorFront)" role="img" aria-label="Soft grey dotted texture"/>

      <g role="img" aria-label="Photo of a woman sleeping peacefully on a white pillow">
        <rect x="70" y="54" width="427" height="240" fill="url(#sleeperFill)"/>
        <rect x="70" y="54" width="427" height="240" fill="url(#sleeperFade)"/>
      </g>

      <g class="brand">
        <circle class="brand-dot" cx="72" cy="48" r="26"/>
        <text class="brand-name" x="72" y="103" text-anchor="middle">WILLOW NEST</text>
      </g>

      <text class="tagline" x="475" y="36" text-anchor="end"><tspan class="t-lead">for a </tspan><tspan class="t-main">peaceful night sleep</tspan></text>
      <text class="subline" x="475" y="57" text-anchor="end">Terry Cloth Waterproof Mattress Protection</text>

      <g class="checklist">
        <path class="check-mark" d="M22 247 l3 4 l6 -9"/>
        <text class="check-item" x="37" y="253">FIVE SIDED PROTECTION</text>
        <path class="check-mark" d="M22 271 l3 4 l6 -9"/>
        <text class="check-item" x="37" y="277">ELASTIC CORNERS FOR EXTRA GRIP</text>
        <path class="check-mark" d="M22 295 l3 4 l6 -9"/>
        <text class="check-item" x="37" y="301">NO SLIP MATTRESS PROTECTION</text>
      </g>

      <!-- Row 1 -->
      <g transform="translate(71 399)">
        <text class="badge-label"><textPath href="#arcL" startOffset="50%" text-anchor="middle">QUITE- NO NOISE</textPath></text>
        <circle class="badge-disc" r="41"/><circle class="badge-ring" r="31"/>
        <path class="badge-line" d="M-4 -16 q-10 14 -4 22 q6 6 14 2 M4 6 q6 -8 -2 -20"/>
        <line class="badge-slash" x1="-22" y1="-22" x2="22" y2="22"/>
      </g>
      <g transform="translate(188 399)">
        <text class="badge-label"><textPath href="#arcL" startOffset="50%" text-anchor="middle">ULTRA SOFT TERRY CLOTH</textPath></text>
        <circle class="badge-disc" r="41"/><circle class="badge-ring" r="31"/>
        <path class="badge-glyph" d="M16 -18 C4 -16 -10 -4 -12 12 L-16 20 L-13 21 L-9 14 C6 12 14 0 16 -18 Z"/>
      </g>
      <g transform="translate(305 399)">
        <text class="badge-label"><textPath href="#arcL" startOffset="50%" text-anchor="middle">WATERPROOF</textPath></text>
        <circle class="badge-disc" r="41"/><circle class="badge-ring" r="31"/>
        <path class="badge-glyph" d="M0 -17 C6 -6 11 0 11 7 A11 11 0 0 1 -11 7 C-11 0 -6 -6 0 -17 Z"/>
        <line class="badge-slash" x1="-22" y1="-22" x2="22" y2="22"/>
      </g>
      <g transform="translate(422 399)">
        <text class="badge-label"><textPath href="#arcL" startOffset="50%" text-anchor="middle">SWEAT STAIN BLOCKER</textPath></text>
        <circle class="badge-disc" r="41"/><circle class="badge-ring" r="31"/>
        <circle class="badge-glyph" r="11"/><circle class="badge-glyph" cx="-14" cy="-6" r="3"/><circle class="badge-glyph" cx="13" cy="9" r="3"/><circle class="badge-glyph" cx="6" cy="-15" r="2.5"/>
        <line class="badge-slash" x1="-22" y1="-22" x2="22" y2="22"/>
      </g>

      <!-- Row 2 -->
      <g transform="translate(71 519)">
        <text class="badge-label"><textPath href="#arcL" startOffset="50%" text-anchor="middle">WASHABLE</textPath></text>
        <circle class="badge-disc" r="41"/><circle class="badge-ring" r="31"/>
        <rect class="badge-glyph" x="-15" y="-19" width="30" height="36" rx="3"/>
        <circle r="8" fill="none" stroke="var(--magenta)" stroke-width="2.5" cy="2"/>
        <rect x="-10" y="-15" width="6" height="3" fill="var(--magenta)"/>
      </g>
      <g transform="translate(188 519)">
        <text class="badge-label"><textPath href="#arcL" startOffset="50%" text-anchor="middle">DUST MITE &amp; BED BUG DEFENSE</textPath></text>
        <circle class="badge-disc" r="41"/><circle class="badge-ring" r="31"/>
        <ellipse class="badge-glyph" rx="9" ry="13" transform="rotate(35)"/>
        <path class="badge-line" d="M-14 -4 l-6 -3 M14 4 l6 3 M-8 -12 l-5 -6 M8 12 l5 6"/>
        <line class="badge-slash" x1="-22" y1="-22" x2="22" y2="22"/>
      </g>
      <g transform="translate(305 519)">
        <text class="badge-label"><textPath href="#arcL" startOffset="50%" text-anchor="middle">ALLERGEN FREE</textPath></text>
        <circle class="badge-disc" r="41"/><circle class="badge-ring" r="31"/>
        <circle class="badge-glyph" cx="-8" cy="-8" r="4"/><circle class="badge-glyph" cx="8" cy="-4" r="5"/><circle class="badge-glyph" cx="-4" cy="10" r="5"/><circle class="badge-glyph" cx="11" cy="11" r="2.5"/><circle class="badge-glyph" cx="-14" cy="4" r="2"/>
        <line class="badge-slash" x1="-22" y1="-22" x2="22" y2="22"/>
      </g>
      <g transform="translate(422 519)">
        <text class="badge-label"><textPath href="#arcL" startOffset="50%" text-anchor="middle">BACTERIA/MOLD/MILDEW FREE</textPath></text>
        <circle class="badge-disc" r="41"/><circle class="badge-ring" r="31"/>
        <circle class="badge-glyph" r="9"/>
        <path class="badge-line" d="M0 -9 v-7 M0 9 v7 M-9 0 h-7 M9 0 h7 M-6 -6 l-5 -5 M6 6 l5 5 M6 -6 l5 -5 M-6 6 l-5 5"/>
        <line class="badge-slash" x1="-22" y1="-22" x2="22" y2="22"/>
      </g>

      <text class="fit-note" x="250" y="611" text-anchor="middle">FITS CAL KING MATRESS</text>
    </svg>
  </section>

  <!-- BACK -->
  <section class="sheet sheet--back" aria-label="Sell sheet back">
    <svg viewBox="0 0 497 643" xmlns="http://www.w3.org/2000/svg">
      <defs>
        <linearGradient id="floorBack" x1="0" y1="0" x2="0" y2="1">
          <stop offset="0" stop-color="#ffffff"/>
          <stop offset="0.25" stop-color="#eeeef0"/>
          <stop offset="1" stop-color="#e3e3e6"/>
        </linearGradient>
        <radialGradient id="terryA" cx="0.4" cy="0.4" r="0.7">
          <stop offset="0" stop-color="#ffffff"/>
          <stop offset="1" stop-color="#dcdcde"/>
        </radialGradient>
        <radialGradient id="terryB" cx="0.5" cy="0.45" r="0.7">
          <stop offset="0" stop-color="#fbfbfb"/>
          <stop offset="1" stop-color="#cfcfd3"/>
        </radialGradient>
        <radialGradient id="pillowFill" cx="0.5" cy="0.4" r="0.6">
          <stop offset="0" stop-color="#ffffff"/>
          <stop offset="1" stop-color="#d9d9dc"/>
        </radialGradient>
        <path id="arcS2" d="M -29.5 20.6 A 36 36 0 1 1 29.5 20.6"/>
      </defs>

      <rect class="steps-band" x="0" y="0" width="497" height="208"/>
      <text class="steps-title" x="249" y="46" text-anchor="middle">3 SIMPLE STEPS TO INSTALL</text>

      <g class="step">
        <circle class="step-disc" cx="98" cy="108" r="48"/>
        <text class="step-text" x="98" y="106" text-anchor="middle">STEP 1</text>
        <text class="step-text" x="98" y="118" text-anchor="middle">GOES HERE</text>
      </g>
      <path class="step-arrow" d="M157 102 q16 10 32 2 m-5 -4 l5 4 l-5 3"/>
      <g class="step">
        <circle class="step-disc" cx="249" cy="108" r="48"/>
        <text class="step-text" x="249" y="106" text-anchor="middle">STEP 2</text>
        <text class="step-text" x="249" y="118" text-anchor="middle">GOES HERE</text>
      </g>
      <path class="step-arrow" d="M308 102 q16 10 32 2 m-5 -4 l5 4 l-5 3"/>
      <g class="step">
        <circle class="step-disc" cx="402" cy="108" r="48"/>
        <text class="step-text" x="402" y="106" text-anchor="middle">STEP 3</text>
        <text class="step-text" x="402" y="118" text-anchor="middle">GOES HERE</text>
      </g>

      <rect x="0" y="477" width="497" height="166" fill="url(#floorBack)" role="img" aria-label="Soft grey dotted texture"/>

      <g class="fabric">
        <circle cx="90" cy="250" r="74" fill="url(#terryA)" stroke="var(--magenta-soft)" stroke-width="6" role="img" aria-label="Close-up photo of white terry cloth"/>
        <circle cx="143" cy="334" r="66" fill="url(#terryB)" stroke="var(--purple)" stroke-width="6" role="img" aria-label="Photo of the cover fitted over a mattress corner"/>
      </g>

      <g transform="translate(274 260)">
        <text class="badge-label badge-label--small"><textPath href="#arcS2" startOffset="50%" text-anchor="middle">WATERPROOF</textPath></text>
        <circle class="badge-disc" r="30"/><circle class="badge-ring" r="22"/>
        <path class="badge-glyph" d="M0 -12 C4 -4 8 0 8 5 A8 8 0 0 1 -8 5 C-8 0 -4 -4 0 -12 Z"/>
        <line class="badge-slash" x1="-15" y1="-15" x2="15" y2="15"/>
      </g>
      <g transform="translate(358 260)">
        <text class="badge-label badge-label--small"><textPath href="#arcS2" startOffset="50%" text-anchor="middle">SWEAT STAIN BLOCKER</textPath></text>
        <circle class="badge-disc" r="30"/><circle class="badge-ring" r="22"/>
        <circle class="badge-glyph" r="8"/><circle class="badge-glyph" cx="-10" cy="-4" r="2"/><circle class="badge-glyph" cx="9" cy="7" r="2"/>
        <line class="badge-slash" x1="-15" y1="-15" x2="15" y2="15"/>
      </g>
      <g transform="translate(443 260)">
        <text class="badge-label badge-label--small"><textPath href="#arcS2" startOffset="50%" text-anchor="middle">NO DUST MITES &amp; BED BUGS</textPath></text>
        <circle class="badge-disc" r="30"/><circle class="badge-ring" r="22"/>
        <ellipse class="badge-glyph" rx="6" ry="9" transform="rotate(35)"/>
        <line class="badge-slash" x1="-15" y1="-15" x2="15" y2="15"/>
      </g>
      <g transform="translate(274 348)">
        <text class="badge-label badge-label--small"><textPath href="#arcS2" startOffset="50%" text-anchor="middle">NO NOISE &amp; SUPER SOFT</textPath></text>
        <circle class="badge-disc" r="30"/><circle class="badge-ring" r="22"/>
        <path class="badge-line" d="M-3 -11 q-7 10 -3 15 q4 4 10 1 M3 4 q4 -6 -1 -14"/>
        <line class="badge-slash" x1="-15" y1="-15" x2="15" y2="15"/>
      </g>
      <g transform="translate(358 348)">
        <text class="badge-label badge-label--small"><textPath href="#arcS2" startOffset="50%" text-anchor="middle">WASHABLE</textPath></text>
        <circle class="badge-disc" r="30"/><circle class="badge-ring" r="22"/>
        <rect class="badge-glyph" x="-10" y="-13" width="20" height="25" rx="2"/>
        <circle r="5.5" cy="1" fill="none" stroke="var(--magenta)" stroke-width="2"/>
      </g>
      <g transform="translate(443 348)">
        <text class="badge-label badge-label--small"><textPath href="#arcS2" startOffset="50%" text-anchor="middle">ALLERGEN FREE</textPath></text>
        <circle class="badge-disc" r="30"/><circle class="badge-ring" r="22"/>
        <circle class="badge-glyph" cx="-6" cy="-6" r="3"/><circle class="badge-glyph" cx="6" cy="-3" r="3.5"/><circle class="badge-glyph" cx="-3" cy="7" r="3.5"/>
        <line class="badge-slash" x1="-15" y1="-15" x2="15" y2="15"/>
      </g>

      <text class="sizes-title" x="245" y="445" text-anchor="middle">AVAILABLE IN THESE SIZES:</text>
      <text class="sizes-list" x="245" y="467" text-anchor="middle">CAL KING, KING, QUEEN, DOUBLE, FULL, TWIN, TWIN XL</text>
      <line class="rule" x1="20" y1="477" x2="477" y2="477"/>

      <path d="M50 540 Q140 515 245 522 Q250 560 238 600 Q140 610 48 606 Q60 572 50 540 Z" fill="url(#pillowFill)" role="img" aria-label="Photo of a white pillow"/>

      <text class="offer-title" x="281" y="539">WE ALSO OFFER:</text>
      <text class="offer-text" x="281" y="565">Willow Nest Pillows</text>
      <text class="offer-text" x="281" y="589">and Pillow Cases</text>
    </svg>
  </section>

</main>
</body>
</html>
```